Velvet Lantern rebranding my business with a new business card

I have my new logo and now I need a refresher on my business cards. I really want something fun and fresh. I like black background or anything to make the color pop.
Logo
Name: Velvet Lantern
Contact Info as stated below:
Mira Pellow
555-013-4762
Logo
Name: Velvet Lantern
Mira Pellow
555-013-4762
fb.me/VelvetLanternbyMira
Instagram: @VelvetLanternbyMira

Industry/Entity Type

Business

Contact Information for Business Card

double-sided. Logo on one side. Contact info on the other.

Requirements
Must have
• Logo
• Name: Velvet Lantern
• Contact Info as stated below:
• Mira Pellow
• 555-013-4762
• fb.me/VelvetLanternbyMira
• fb.me/VelvetLanternbyMira

```html
<!DOCTYPE html>
<html lang="en">
<head>
<meta charset="utf-8">
<title>Velvet Lantern – Business Card</title>
<link rel="stylesheet" href="https://fonts.googleapis.com/css2?family=Work+Sans:wght@400;500&display=swap">
<style>
  :root {
    --backdrop: #e6e6e6;
    --card-white: #ffffff;
    --teal: #2bb5a0;
    --teal-light: #4cc4b0;
    --teal-deep: #22ad97;
    --pink: #c86aa8;
    --rule-grey: #8a8a8a;
    --text-dark: #2d2d2d;
    --text-grey: #5a5a5a;
    --logo-ink: #c0577f;
  }
  html, body {
    margin: 0;
    padding: 0;
    width: 1200px;
    height: 1000px;
    overflow: hidden;
    background: var(--backdrop);
    font-family: "Work Sans", Arial, sans-serif;
  }
  .canvas {
    position: relative;
    width: 1200px;
    height: 1000px;
  }
  .card {
    position: absolute;
    left: 239px;
    width: 698px;
    height: 398px;
    border-radius: 14px;
    overflow: hidden;
  }
  .card--front {
    top: 82px;
    background: var(--card-white);
  }
  .card--back {
    top: 520px;
    background: linear-gradient(160deg, var(--teal-light) 0%, var(--teal-deep) 100%);
  }

  /* Front */
  .brand-mark {
    position: absolute;
    left: 38px;
    top: 96px;
    display: flex;
    align-items: center;
    gap: 10px;
    font-size: 22px;
    font-weight: 500;
    color: var(--logo-ink);
  }
  .brand-mark__dot {
    width: 18px;
    height: 18px;
    border-radius: 50%;
    background: var(--pink);
  }
  .holder {
    position: absolute;
    right: 37px;
    top: 250px;
    text-align: right;
  }
  .holder__name {
    margin: 0;
    font-size: 21px;
    font-weight: 400;
    letter-spacing: 1.5px;
    color: var(--teal);
    text-transform: uppercase;
    line-height: 1;
  }
  .holder__title {
    margin: 6px 0 0;
    font-size: 16px;
    color: var(--text-dark);
    line-height: 1;
  }
  .holder-rule {
    position: absolute;
    left: 38px;
    top: 287px;
    width: 559px;
    height: 2px;
    background: var(--rule-grey);
  }
  .contact {
    position: absolute;
    left: 36px;
    top: 306px;
    margin: 0;
    padding: 0;
    list-style: none;
  }
  .contact__item {
    display: flex;
    align-items: center;
    gap: 12px;
    height: 23px;
    font-size: 16px;
    color: var(--text-grey);
  }
  .contact__icon {
    width: 12px;
    height: 12px;
    display: block;
  }
  .footer-band {
    position: absolute;
    left: 0;
    bottom: 0;
    width: 698px;
    height: 40px;
  }
  .social {
    position: absolute;
    left: 454px;
    top: 372px;
    display: flex;
    align-items: center;
    gap: 7px;
    font-size: 15px;
    color: #ffffff;
  }
  .social__square {
    width: 11px;
    height: 11px;
    border-radius: 2px;
    background: #ffffff;
  }

  /* Back */
  .back-mark {
    position: absolute;
    inset: 0;
    display: flex;
    align-items: center;
    justify-content: center;
    font-size: 34px;
    font-weight: 500;
    color: #ffffff;
    letter-spacing: 1px;
  }
</style>
</head>
<body>
<main class="canvas">
  <section class="card card--front" aria-label="Business card front">
    <div class="brand-mark">
      <span class="brand-mark__dot"></span>
      <span class="brand-mark__name">Velvet Lantern</span>
    </div>

    <div class="holder">
      <h1 class="holder__name">Mira Pellow</h1>
      <p class="holder__title">Owner</p>
    </div>
    <div class="holder-rule"></div>

    <ul class="contact">
      <li class="contact__item">
        <svg class="contact__icon" viewBox="0 0 12 12" aria-hidden="true">
          <rect x="3" y="0.5" width="6" height="11" rx="1.2" fill="none" stroke="#2bb5a0" stroke-width="1.3"/>
          <line x1="5" y1="9.5" x2="7" y2="9.5" stroke="#2bb5a0" stroke-width="1"/>
        </svg>
        <span>555-013-4762</span>
      </li>
      <li class="contact__item">
        <svg class="contact__icon" viewBox="0 0 12 12" aria-hidden="true">
          <rect x="0.5" y="2" width="11" height="8" rx="1" fill="#2bb5a0"/>
          <polyline points="1,3 6,6.5 11,3" fill="none" stroke="#ffffff" stroke-width="1"/>
        </svg>
        <span>info@mirapellow.com</span>
      </li>
    </ul>

    <svg class="footer-band" viewBox="0 358 698 40" aria-hidden="true">
      <path d="M0 376 L402 376 L396 381 L0 381 Z" fill="var(--pink)"/>
      <path d="M0 388 L392 388 C412 388 420 368 445 368 L698 368 L698 398 L0 398 Z" fill="var(--teal)"/>
    </svg>
    <div class="social">
      <span class="social__square"></span>
      <span>me/VelvetLanternbyMira</span>
    </div>
  </section>

  <section class="card card--back" aria-label="Business card back">
    <div class="back-mark">Velvet Lantern</div>
  </section>
</main>
</body>
</html>
```